VELMOR Website Design

We need a website designed for our company VELMOR. We are a luxury lifestyle club that will provide benefits and services for our members. The site should be clean & sleek, preferably using black and white (or darker colors). (example sites: stravenhall.example, plinth.example)

Here is a link of a sample page I did using wix. (https://dunmere7.sitehostly.example/mysite) This can be used to get a general idea.

Target Market(s)

Upper Middle Class in the United States

Number of Pages Required

5+ page

Font styles to use
Sans Serif
Other font styles liked:
• Arial (or other similar fonts)

Requirements
Must have
• A clean design that is eye-catching and speaks to our company.
Nice to have
• Ideas for copy.

```html
<!DOCTYPE html>
<html lang="en">
<head>
<meta charset="utf-8">
<title>VELMOR — Luxury Lifestyle Club</title>
<link href="https://fonts.googleapis.com/css2?family=Poppins:wght@400;500;600;700&display=swap" rel="stylesheet">
<style>
:root{
  --ink:#0d0d0d;
  --white:#ffffff;
  --soft:#f2f2f2;
  --text:#333333;
  --muted:#555555;
  --footer:#1b1b1b;
  --star:#f29a1f;
  --hero-a:#3a2a30;
  --hero-b:#1a1418;
}
*{margin:0;padding:0;box-sizing:border-box}
html,body{width:1200px;height:2857px;overflow:hidden;background:var(--white)}
body{font-family:'Poppins',Arial,sans-serif;color:var(--text);position:relative}
.abs{position:absolute}
.btn{position:absolute;display:flex;align-items:center;justify-content:center;border-radius:30px;font-weight:600;font-size:17px}
.btn-dark{background:var(--ink);color:var(--white)}
.btn-light{background:var(--white);color:var(--ink)}
.photo{position:absolute}

/* hero */
.hero{position:absolute;left:0;top:0;width:1200px;height:667px;background:radial-gradient(ellipse at 55% 40%,#6a4a50 0%,var(--hero-a) 40%,var(--hero-b) 100%)}
.hero::after{content:"";position:absolute;inset:0;background:linear-gradient(90deg,rgba(40,120,140,0) 40%,rgba(40,170,190,.25) 65%,rgba(0,0,0,0) 80%)}
.topbar{position:absolute;left:0;top:0;width:1200px;height:48px;color:var(--white);font-size:13px;z-index:2}
.topbar span{position:absolute;top:13px;white-space:nowrap}
.topbar svg{position:absolute}
.nav{position:absolute;left:80px;top:48px;width:1040px;height:70px;background:var(--white);z-index:2}
.logo{position:absolute;left:21px;top:10px;font-size:40px;font-weight:500;color:var(--ink);letter-spacing:1px}
.nav-links{position:absolute;top:23px;font-size:16px;color:var(--text)}
.nav-links a{position:absolute;white-space:nowrap;color:inherit;text-decoration:none}
.hero-title{position:absolute;left:0;width:1200px;top:296px;text-align:center;color:var(--white);font-size:52px;font-weight:700;z-index:2}
.hero-text{position:absolute;left:0;width:1200px;top:370px;text-align:center;color:var(--white);font-size:18px;font-weight:500;line-height:27px;z-index:2}
.arrow{position:absolute;width:42px;height:42px;border-radius:50%;background:rgba(0,0,0,.55);z-index:2}

/* services */
.h2{position:absolute;font-size:32px;font-weight:600;color:var(--ink);white-space:nowrap}
.card-label{position:absolute;font-size:20px;font-weight:500;color:var(--text)}
.card-icon{position:absolute;width:48px;height:48px;border-radius:50%;background:#3a3a3a}

/* cta */
.cta{position:absolute;left:0;top:1490px;width:1200px;height:207px;background:linear-gradient(90deg,#141414,#2a2424 50%,#141414)}
.cta p{position:absolute;left:110px;top:73px;color:var(--white);font-size:20px;line-height:31px}

/* about */
.about{position:absolute;left:0;top:1697px;width:615px;height:440px;background:var(--soft)}
.body-text{position:absolute;font-size:15px;line-height:29px;color:var(--muted);white-space:nowrap}

/* footer */
.footer{position:absolute;left:0;top:2648px;width:1200px;height:209px;background:var(--footer);color:var(--white)}
.social{position:absolute;width:30px;height:30px;border-radius:50%;border:2px solid var(--white)}
</style>
</head>
<body>

<header class="hero" role="img" aria-label="Photo of friends laughing together at a lounge bar at night"></header>

<div class="topbar">
  <svg style="left:86px;top:15px" width="16" height="16" viewBox="0 0 24 24"><path fill="#fff" d="M6.6 10.8a15 15 0 0 0 6.6 6.6l2.2-2.2c.3-.3.7-.4 1-.2 1.1.4 2.3.6 3.6.6.6 0 1 .4 1 1V20c0 .6-.4 1-1 1A17 17 0 0 1 3 4c0-.6.4-1 1-1h3.5c.6 0 1 .4 1 1 0 1.3.2 2.5.6 3.6.1.3 0 .7-.2 1z"/></svg>
  <span style="left:112px">+1 5550148822</span>
  <svg style="left:218px;top:14px" width="3" height="20"><rect width="3" height="20" fill="#fff"/></svg>
  <svg style="left:238px;top:12px" width="16" height="22" viewBox="0 0 24 32"><path fill="#fff" d="M12 0C5.4 0 0 5.4 0 12c0 9 12 20 12 20s12-11 12-20C24 5.4 18.6 0 12 0zm0 17a5 5 0 1 1 0-10 5 5 0 0 1 0 10z"/></svg>
  <span style="left:262px">#27, Larkspur Ave, Harborview, FL 3318</span>
  <svg style="left:800px;top:14px" width="20" height="16" viewBox="0 0 24 18"><path fill="#fff" d="M0 0h24v2L12 10 0 2zM0 4l12 8 12-8v14H0z"/></svg>
  <span style="left:830px">info@velmor.example</span>
  <svg style="left:986px;top:14px" width="2" height="20"><rect width="2" height="20" fill="#fff"/></svg>
  <svg style="left:1008px;top:10px" width="110" height="28">
    <circle cx="14" cy="14" r="12" fill="none" stroke="#fff" stroke-width="2"/>
    <circle cx="50" cy="14" r="12" fill="none" stroke="#fff" stroke-width="2"/>
    <circle cx="86" cy="14" r="12" fill="none" stroke="#fff" stroke-width="2"/>
  </svg>
</div>

<nav class="nav">
  <div class="logo">VELMOR</div>
  <div class="nav-links">
    <a style="left:349px;font-weight:600;color:var(--ink)">Home</a>
    <a style="left:423px">About Us</a>
    <a style="left:518px">Services</a>
    <a style="left:610px">Benefits</a>
    <a style="left:699px">Contact Us</a>
  </div>
  <svg class="abs" style="left:808px;top:26px" width="20" height="20" viewBox="0 0 24 24"><circle cx="10" cy="10" r="7" fill="none" stroke="#222" stroke-width="3"/><path d="M15 15l7 7" stroke="#222" stroke-width="3"/></svg>
  <div class="btn btn-dark" style="left:878px;top:13px;width:141px;height:38px;font-size:15px">Request Quote</div>
</nav>

<h1 class="hero-title">WELCOME TO VELMOR</h1>
<p class="hero-text">Lorem ipsum dolor sit amet, consectetur adipiscing elit, sed do eiusmod<br>tempor incididunt ut labore et dolore magna aliqua.</p>
<div class="btn btn-light" style="left:528px;top:451px;width:146px;height:48px;z-index:2">About Us</div>
<div class="arrow" style="left:29px;top:330px"><svg width="42" height="42"><path d="M24 14l-7 7 7 7" stroke="#fff" stroke-width="3" fill="none"/></svg></div>
<div class="arrow" style="left:1129px;top:330px"><svg width="42" height="42"><path d="M18 14l7 7-7 7" stroke="#fff" stroke-width="3" fill="none"/></svg></div>

<!-- What we do -->
<h2 class="h2" style="left:80px;top:744px">WHAT WE DO</h2>
<div class="abs" style="left:318px;top:739px;width:2px;height:54px;background:#999"></div>
<p class="body-text" style="left:352px;top:738px;font-size:16px;line-height:28px">Lorem ipsum dolor sit amet, consectetur adipiscing elit,<br>sed do eiusmod tempor incididunt ut labore</p>
<div class="btn btn-dark" style="left:970px;top:745px;width:148px;height:40px;font-size:16px">All Services</div>

<div class="photo" style="left:80px;top:827px;width:330px;height:205px;background:linear-gradient(135deg,#3d3d3d,#c9cdd2 60%,#6e6a66)" role="img" aria-label="Photo of hands reviewing financial documents with a pen"></div>
<div class="photo" style="left:434px;top:827px;width:330px;height:205px;background:linear-gradient(135deg,#0e1a2e,#2b4468 60%,#0c1524)" role="img" aria-label="Photo of a stock market chart on a screen"></div>
<div class="photo" style="left:789px;top:827px;width:330px;height:205px;background:linear-gradient(135deg,#3c4a2a,#6c5a48 55%,#2a3220)" role="img" aria-label="Photo of guests dining at an outdoor evening party"></div>
<div class="photo" style="left:80px;top:1126px;width:330px;height:206px;background:linear-gradient(135deg,#2a4a6e,#c8b8a8 55%,#3e5a7a)" role="img" aria-label="Photo of a smiling couple receiving house keys"></div>
<div class="photo" style="left:434px;top:1126px;width:330px;height:206px;background:linear-gradient(135deg,#e8e6e2,#cfcbc5 55%,#7a5c44)" role="img" aria-label="Photo of a concierge desk with a reception bell"></div>
<div class="photo" style="left:789px;top:1126px;width:330px;height:206px;background:linear-gradient(180deg,#9cb8d6,#d8d8d8 55%,#5a5e62)" role="img" aria-label="Photo of travellers boarding a private jet on a red carpet"></div>

<div class="card-icon" style="left:104px;top:1046px"></div><div class="card-label" style="left:170px;top:1055px">Accounting Services</div>
<div class="card-icon" style="left:458px;top:1046px"></div><div class="card-label" style="left:525px;top:1055px">Investment Services</div>
<div class="card-icon" style="left:812px;top:1046px"></div><div class="card-label" style="left:879px;top:1055px">Private Events</div>
<div class="card-icon" style="left:104px;top:1345px"></div><div class="card-label" style="left:170px;top:1354px">Real Estate Services</div>
<div class="card-icon" style="left:458px;top:1345px"></div><div class="card-label" style="left:525px;top:1354px">24/7 Concierge</div>
<div class="card-icon" style="left:812px;top:1345px"></div><div class="card-label" style="left:879px;top:1354px">Private Jet Travel</div>

<!-- CTA band -->
<section class="cta" role="img" aria-label="Dark photo of friends celebrating at a party">
  <p>Lorem ipsum dolor sit amet, consectetur adipiscing elit, sed do eiusmod<br>tempor incididunt ut labore et dolore magna aliqua.</p>
</section>
<div class="btn btn-light" style="left:863px;top:1566px;width:230px;height:53px;font-size:18px">Request Quote</div>

<!-- About -->
<section class="about"></section>
<h2 class="h2" style="left:80px;top:1783px">WE ARE VELMOR</h2>
<p class="body-text" style="left:80px;top:1841px">Built in the image of a"Multi-Family Office", VELMOR provides<br>members with access to just about any service, experience, and<br>event desirable.<br>VELMOR is truly the most exclusive lifestyle club out there.</p>
<div class="btn btn-dark" style="left:80px;top:1991px;width:177px;height:57px;font-size:18px">Apply</div>
<div class="photo" style="left:615px;top:1697px;width:585px;height:440px;background:radial-gradient(circle at 30% 30%,#c8904a,#5a3a2a 55%,#1e1410)" role="img" aria-label="Photo of women toasting with champagne glasses"></div>

<!-- Reviews -->
<h2 class="h2" style="left:78px;top:2220px;font-size:33px">CLIENTS’ REVIEW</h2>
<p class="body-text" style="left:78px;top:2276px;line-height:28px">Lorem ipsum dolor sit amet, consectetur adipisicing elit. Possimus,<br>aperiam consequuntur dolore mollitia laborum officia</p>
<div class="photo" style="left:80px;top:2362px;width:53px;height:54px;background:linear-gradient(160deg,#b0a090,#4a4a55)" role="img" aria-label="Portrait of the reviewer"></div>
<div class="abs" style="left:158px;top:2355px;font-size:22px;font-weight:600;color:var(--ink)">Outstanding Quality</div>
<svg class="abs" style="left:158px;top:2390px" width="110" height="20" viewBox="0 0 110 20">
  <g fill="var(--star)">
    <path id="st" d="M9 1l2.4 5.3 5.6.6-4.2 3.8 1.2 5.6L9 13.5 4 16.3l1.2-5.6L1 6.9l5.6-.6z"/>
    <use href="#st" x="21"/><use href="#st" x="42"/><use href="#st" x="63"/><use href="#st" x="84"/>
  </g>
</svg>
<svg class="abs" style="left:499px;top:2366px" width="46" height="36" viewBox="0 0 46 36"><path d="M10 2a9 9 0 1 0 9 9c0 10-7 18-14 22M34 2a9 9 0 1 0 9 9c0 10-7 18-14 22" fill="none" stroke="#222" stroke-width="2.5"/></svg>
<p class="body-text" style="left:80px;top:2426px;line-height:27px;color:var(--text)">Sed ut perspiciatis unde omnis iste natus error sit voluptatem<br>accusantium doloremque laudantium, totam rem aperiam, eaque<br>ipsa quae ab illo inventore veritatis et</p>
<div class="abs" style="left:80px;top:2519px;font-size:17px;font-weight:600;color:var(--ink)">- Aldous Wren</div>
<svg class="abs" style="left:80px;top:2558px" width="75" height="30">
  <circle cx="15" cy="15" r="14" fill="var(--ink)"/><path d="M18 9l-6 6 6 6" stroke="#fff" stroke-width="2.5" fill="none"/>
  <circle cx="57" cy="15" r="14" fill="var(--ink)"/><path d="M54 9l6 6-6 6" stroke="#fff" stroke-width="2.5" fill="none"/>
</svg>

<div class="photo" style="left:613px;top:2227px;width:505px;height:187px;background:linear-gradient(135deg,#e4e2dc,#d4d8cc 50%,#e8e4d8)" role="img" aria-label="Map showing the club location"></div>

<div class="abs" style="left:613px;top:2452px;font-size:26px;font-weight:600;color:var(--ink)">Call Us</div>
<div class="abs" style="left:613px;top:2500px;font-size:28px;font-weight:500;color:var(--ink)">+1 5550148822</div>
<svg class="abs" style="left:874px;top:2460px" width="18" height="24" viewBox="0 0 24 32"><path fill="#111" d="M12 0C5.4 0 0 5.4 0 12c0 9 12 20 12 20s12-11 12-20C24 5.4 18.6 0 12 0zm0 17a5 5 0 1 1 0-10 5 5 0 0 1 0 10z"/></svg>
<p class="body-text" style="left:920px;top:2458px;font-size:16px;line-height:27px">#27, Larkspur Ave,<br>Harborview, FL 3318</p>
<svg class="abs" style="left:874px;top:2535px" width="22" height="17" viewBox="0 0 24 18"><path fill="#111" d="M0 0h24v2L12 10 0 2zM0 4l12 8 12-8v14H0z"/></svg>
<div class="abs" style="left:920px;top:2530px;font-size:16px;color:var(--muted)">info@velmor.example</div>

<!-- Footer -->
<footer class="footer">
  <div class="social" style="left:537px;top:46px"></div>
  <div class="social" style="left:584px;top:46px"></div>
  <div class="social" style="left:631px;top:46px"></div>
  <div class="abs" style="left:0;width:1200px;top:104px;text-align:center;font-size:16px;font-weight:600">
    <span style="margin:0 12px">Home</span><span style="margin:0 12px">About Us</span><span style="margin:0 12px">Services</span><span style="margin:0 12px">Benefits</span><span style="margin:0 12px">Contact Us</span>
  </div>
  <div class="abs" style="left:0;width:1200px;top:143px;text-align:center;font-size:15px">Copyright 2018 | All rights reserved | Privacy Policy | Term &amp; Conditions</div>
</footer>

</body>
</html>
```